Holistic Health Coach needs simple web site design for a new practice

I need a web (re)design for my entire site, Ridgeway Fern Lady. I have a beautiful new blue and green logo that I'd like the site fonts and color scheme to be built around. I'll attach my new logo so you'll know the colors/design feel I'm after.

I want easy navigation for my mostly text based site, widgets for my social media pages and a clean, fun, light feel for the site.

Target Market(s)

People looking to take charge of their own health, and who may need my coaching services to obtain optimal wellness.

Industry/Entity Type

Health

Coding

Coded - Design and coding required

Number of Pages Required

5+ page

Font styles to use
Script

Colors
33b8a4
33a6d7
ffffff

Requirements
Must have
• Must incorporate my logo design, as well as same/similar fonts and color scheme.
• I'd like it to stay as close to the current design as possible.
Nice to have
• Would love to incorporate a hover over menu (for example, when a user hovers over "About", they will see the submenu in a floating design.
Should not have
• No dark colors or masculine feel

```html
<!DOCTYPE html>
<html lang="en">
<head>
<meta charset="utf-8">
<title>Ridgeway Fern Lady</title>
<link href="https://fonts.googleapis.com/css2?family=Roboto:wght@400;500;700&family=Oswald:wght@400;500&display=swap" rel="stylesheet">
<style>
:root{
  --blue:#3a93d8;
  --teal:#33b8a4;
  --green:#8bc34a;
  --ink:#333333;
  --muted:#555555;
  --page:#ececec;
  --card:#ffffff;
  --line:#e2e2e2;
  --footer-light:#f2f2f2;
  --footer-dark:#2a2a2a;
  --orange:#f08a1c;
  --hero-dark:#4e4443;
  --hero-mid:#7a6a66;
  --hero-light:#c7bdb8;
  --share-blue:#4b67a8;
  --share-red:#d24a3a;
  --promo-bg:#eeeeee;
}
*{box-sizing:border-box;margin:0;padding:0}
html,body{width:1200px;height:2835px;overflow:hidden}
body{font-family:"Roboto",Arial,sans-serif;color:var(--ink);background:var(--page);position:relative}
.abs{position:absolute}

/* header */
.site-header{left:0;top:0;width:1200px;height:108px;background:#fff}
.nav-link{top:57px;font-size:16px;color:#222;text-transform:uppercase;letter-spacing:.3px;white-space:nowrap}
.nav-link.active{color:var(--blue)}
.brand{left:520px;top:44px;width:200px;text-align:center;font-size:24px;font-weight:500;color:var(--teal);white-space:nowrap}
.submenu{left:85px;top:108px;width:155px;height:132px;background:rgba(225,225,225,.92);padding:12px 0 0 25px}
.submenu li{list-style:none;font-size:15px;color:#333;line-height:27px;text-transform:uppercase}

/* hero */
.hero{left:0;top:108px;width:1200px;height:540px;background:linear-gradient(100deg,var(--hero-dark) 0%,var(--hero-mid) 35%,var(--hero-light) 55%,#8d7c76 75%,#5b4a45 100%)}
.hero-title{left:121px;top:280px;font-family:"Oswald",Arial,sans-serif;font-size:66px;font-weight:400;color:#fff;line-height:1;white-space:nowrap}
.hero-sub{left:121px;top:360px;font-family:"Oswald",Arial,sans-serif;font-size:36px;color:#fff;line-height:1;white-space:nowrap}
.hero-arrow{top:332px;width:36px;height:36px}

/* posts */
.post{left:104px;width:610px;height:421px;background:var(--card);border:1px solid #ddd;box-shadow:0 1px 3px rgba(0,0,0,.08)}
.post-image{position:absolute;left:10px;top:8px;width:588px;height:205px}
.date-badge{position:absolute;left:10px;top:8px;width:57px;height:67px;background:#111;color:#fff;text-align:center;padding-top:5px}
.date-badge .m{font-size:12px;display:block;text-align:right;padding-right:6px}
.date-badge .d{font-size:22px;display:block;line-height:22px}
.date-badge .y{font-size:10px;display:block}
.post-title{position:absolute;left:20px;top:248px;font-size:15px;color:var(--blue);text-transform:uppercase;font-weight:400}
.post-text{position:absolute;left:20px;top:278px;width:580px;font-size:12.5px;line-height:20px;color:#333}
.post-meta{position:absolute;left:16px;top:345px;font-size:12px;color:#222}
.post-divider{position:absolute;left:0;top:374px;width:100%;height:1px;background:var(--line)}
.share{position:absolute;top:386px;display:flex;align-items:center;gap:5px}
.share .btn{font-size:11px;padding:3px 8px;border:1px solid #ccc;border-radius:3px;background:#f4f4f4;color:#333}
.share .btn.blue{background:var(--share-blue);color:#fff;border-color:var(--share-blue)}
.share .btn.red{color:var(--share-red)}
.share .count{font-size:11px;border:1px solid #ccc;padding:3px 6px;background:#fff}

/* sidebar */
.widget{left:758px;width:340px;background:var(--card);border:1px solid #ddd;box-shadow:0 1px 3px rgba(0,0,0,.08)}
.search-input{position:absolute;left:18px;top:28px;width:196px;height:38px;background:#e4e4e4;font-size:11px;color:#777;padding:14px 12px;font-style:italic}
.search-btn{position:absolute;left:220px;top:28px;width:98px;height:36px;background:var(--blue);color:#fff;font-size:14px;text-align:center;line-height:36px;border-radius:2px}
.widget-title{font-size:20px;color:var(--blue);padding:22px 0 0 28px;text-transform:uppercase;font-weight:400}
.popular-item{position:absolute;left:24px;width:290px;height:82px;border-bottom:1px solid #eee}
.popular-thumb{position:absolute;left:0;top:0;width:95px;height:66px;border:3px solid #fff;box-shadow:0 1px 4px rgba(0,0,0,.3)}
.popular-text{position:absolute;left:104px;top:0;width:180px;font-size:11px;line-height:17px;color:#444}
.popular-text b{display:block;color:var(--blue);font-weight:400;font-size:12.5px}
.band{height:49px;background:var(--green);color:#fff;font-size:21px;padding:13px 0 0 37px;text-transform:uppercase}
.list{padding:12px 0 0 37px;list-style:none}
.list li{font-size:16px;color:#333;height:40px;line-height:40px;display:flex;align-items:center;gap:16px}
.list svg{width:14px;height:14px}

.promo{left:758px;top:2164px;width:340px;height:293px;background:#fff;border:1px solid #ddd;box-shadow:0 1px 3px rgba(0,0,0,.08)}
.promo-inner{position:absolute;left:47px;top:20px;width:246px;height:250px;background:var(--promo-bg);text-align:center}
.promo-head{font-size:15px;font-weight:700;color:#333;line-height:19px;padding-top:10px;text-transform:uppercase}
.promo-head .light{font-weight:400}
.promo-head .blue{color:var(--blue)}
.promo-products{position:absolute;left:12px;top:74px;width:150px;height:100px;background:linear-gradient(90deg,#7a4e93,#c74d8a,#4b8dc8)}
.promo-badge{position:absolute;left:166px;top:70px;width:74px;height:74px;border-radius:50%;background:var(--blue)}
.promo-tag{position:absolute;left:0;top:184px;width:100%;font-size:19px;font-style:italic;color:#333}
.promo-btn{position:absolute;left:54px;top:215px;width:138px;height:28px;background:var(--orange);color:#fff;font-size:14px;font-weight:700;line-height:28px;border-radius:3px}

/* footer */
.footer-links{left:0;top:2510px;width:1200px;height:187px;background:var(--footer-light)}
.footer-col{position:absolute;top:30px}
.footer-col h4{font-size:18px;font-weight:400;color:var(--blue);margin-bottom:16px;padding-bottom:4px;border-bottom:1px solid #ddd;width:200px}
.footer-col li{list-style:none;font-size:12px;line-height:24px;color:#333}
.footer-bar{left:0;top:2697px;width:1200px;height:138px;background:var(--footer-dark)}
.legal{position:absolute;left:104px;top:43px;font-size:13px;color:#fff;line-height:30px}
.social{position:absolute;top:42px;width:44px;height:44px;border-radius:50%;border:2px solid #fff}
</style>
</head>
<body>

<header class="site-header abs">
  <span class="nav-link active abs" style="left:104px">About Mara</span>
  <span class="nav-link abs" style="left:234px">Articles</span>
  <span class="nav-link abs" style="left:352px">Essential Oils</span>
  <span class="brand abs">Ridgeway Fern Lady</span>
  <span class="nav-link abs" style="left:765px">21-Day Sweet Reset Coaching Services</span>
</header>

<section class="hero abs" role="img" aria-label="Photo of a young woman in a white knit hat and scarf in a snowy winter scene"></section>
<h1 class="hero-title abs">RIDGEWAY FERN LADY</h1>
<p class="hero-sub abs">IPSUM IS SIMPLY DUMMY</p>
<svg class="hero-arrow abs" style="left:33px" viewBox="0 0 36 36"><circle cx="18" cy="18" r="18" fill="#fff"/><path d="M21 11l-7 7 7 7" stroke="#333" stroke-width="3" fill="none"/></svg>
<svg class="hero-arrow abs" style="left:1130px" viewBox="0 0 36 36"><circle cx="18" cy="18" r="18" fill="#fff"/><path d="M15 11l7 7-7 7" stroke="#333" stroke-width="3" fill="none"/></svg>

<ul class="submenu abs">
  <li>Sub Menu 1</li><li>Sub Menu 2</li><li>Sub Menu 3</li><li>Sub Menu 4</li>
</ul>

<!-- posts -->
<article class="post abs" style="top:705px">
  <div class="post-image" role="img" aria-label="Photo of a woman on a beach by the sea" style="background:linear-gradient(180deg,#b9d3dc,#6f9aa3 55%,#d8d1c3)"></div>
  <div class="date-badge"><span class="m">Dec</span><span class="d">20</span><span class="y">2015</span></div>
  <h2 class="post-title">Lifestyles of the Tired and Wired</h2>
  <p class="post-text">Lorem Ipsum has been the industry's standard dummy text ever since the 1500s, when an unknown printer took a galley of type and scrambled it to make a type specimen book. It has survived not only</p>
  <p class="post-meta">This entry was posted in Fernhouse on 11/01/2015.</p>
  <div class="post-divider"></div>
  <div class="share" style="left:312px"><span class="btn">Post</span><span class="count">0</span></div>
  <div class="share" style="left:420px"><span class="btn blue">Like</span><span class="count">0</span></div>
  <div class="share" style="left:528px"><span class="btn red">+1</span><span class="count">0</span></div>
</article>

<article class="post abs" style="top:1150px">
  <div class="post-image" role="img" aria-label="Photo of a group of smiling friends in sunglasses outdoors" style="background:linear-gradient(180deg,#d9e6ef,#9a8a7e 55%,#5d6c86)"></div>
  <div class="date-badge"><span class="m">Dec</span><span class="d">20</span><span class="y">2015</span></div>
  <h2 class="post-title">April Essential Living Education Series</h2>
  <p class="post-text">Lorem Ipsum has been the industry's standard dummy text ever since the 1500s, when an unknown printer took a galley of type and scrambled it to make a type specimen book. It has survived not only</p>
  <p class="post-meta">This entry was posted in Fernhouse on 11/01/2015.</p>
  <div class="post-divider"></div>
  <div class="share" style="left:312px"><span class="btn">Post</span><span class="count">0</span></div>
  <div class="share" style="left:420px"><span class="btn blue">Like</span><span class="count">0</span></div>
  <div class="share" style="left:528px"><span class="btn red">+1</span><span class="count">0</span></div>
</article>

<article class="post abs" style="top:1593px">
  <div class="post-image" role="img" aria-label="Photo of a group of students standing together under a blue sky" style="background:linear-gradient(180deg,#6fa6dc,#a9c7e6 40%,#7d7466 75%,#4e5a3f)"></div>
  <div class="date-badge"><span class="m">Dec</span><span class="d">20</span><span class="y">2015</span></div>
  <h2 class="post-title">Module 3: A Nice Supplement to the Program</h2>
  <p class="post-text">Lorem Ipsum has been the industry's standard dummy text ever since the 1500s, when an unknown printer took a galley of type and scrambled it to make a type specimen book. It has survived not only</p>
  <p class="post-meta">This entry was posted in Fernhouse and tagged rambler, Trail Wagon on 06/01/2015.</p>
  <div class="post-divider"></div>
  <div class="share" style="left:312px"><span class="btn">Post</span><span class="count">0</span></div>
  <div class="share" style="left:420px"><span class="btn blue">Like</span><span class="count">0</span></div>
  <div class="share" style="left:528px"><span class="btn red">+1</span><span class="count">0</span></div>
</article>

<article class="post abs" style="top:2035px">
  <div class="post-image" role="img" aria-label="Photo of a smiling student in a library with bookshelves" style="background:linear-gradient(90deg,#d8d2c8,#8a6b4e 45%,#5a4232 70%,#8b5a3c)"></div>
  <div class="date-badge"><span class="m">Dec</span><span class="d">20</span><span class="y">2015</span></div>
  <h2 class="post-title">Module 3: A Nice Supplement to the Program</h2>
  <p class="post-text">Lorem Ipsum has been the industry's standard dummy text ever since the 1500s, when an unknown printer took a galley of type and scrambled it to make a type specimen book. It has survived not only</p>
  <p class="post-meta">This entry was posted in Fernhouse and tagged rambler, Trail Wagon on 06/01/2015.</p>
  <div class="post-divider"></div>
  <div class="share" style="left:312px"><span class="btn">Post</span><span class="count">0</span></div>
  <div class="share" style="left:420px"><span class="btn blue">Like</span><span class="count">0</span></div>
  <div class="share" style="left:528px"><span class="btn red">+1</span><span class="count">0</span></div>
</article>

<!-- sidebar -->
<aside class="widget abs" style="top:705px;height:91px">
  <div class="search-input">Search</div>
  <div class="search-btn">Search</div>
</aside>

<aside class="widget abs" style="top:813px;height:569px">
  <h3 class="widget-title">Popular Blogs</h3>
  <div class="popular-item" style="top:78px"><div class="popular-thumb" role="img" aria-label="Thumbnail photo of a woman" style="background:#d7b9a4"></div><p class="popular-text"><b>This is a sample Post 1</b>Lorem ipsum dolor sit amet, consectetuer adipiscing elit, sed diam nonummy nibh...</p></div>
  <div class="popular-item" style="top:178px"><div class="popular-thumb" role="img" aria-label="Thumbnail photo of a desk with documents" style="background:#8c99a8"></div><p class="popular-text"><b>This is a sample Post 1</b>Lorem ipsum dolor sit amet, consectetuer adipiscing elit, sed diam nonummy nibh...</p></div>
  <div class="popular-item" style="top:278px"><div class="popular-thumb" role="img" aria-label="Thumbnail photo of an older couple" style="background:#b8a89a"></div><p class="popular-text"><b>This is a sample Post 1</b>Lorem ipsum dolor sit amet, consectetuer adipiscing elit, sed diam nonummy nibh...</p></div>
  <div class="popular-item" style="top:370px"><div class="popular-thumb" role="img" aria-label="Thumbnail photo of a smiling woman" style="background:#6e5650"></div><p class="popular-text"><b>This is a sample Post 1</b>Lorem ipsum dolor sit amet, consectetuer adipiscing elit, sed diam nonummy nibh...</p></div>
  <div class="popular-item" style="top:470px;border-bottom:0"><div class="popular-thumb" role="img" aria-label="Thumbnail photo of a woman with long hair" style="background:#b08a64"></div><p class="popular-text"><b>This is a sample Post 1</b>Lorem ipsum dolor sit amet, consectetuer adipiscing elit, sed diam nonummy nibh...</p></div>
</aside>

<aside class="widget abs" style="top:1395px;height:391px">
  <h3 class="band">Archives</h3>
  <ul class="list">
    <li><svg viewBox="0 0 14 14"><path d="M2 2l5 5-5 5M7 2l5 5-5 5" stroke="#3a93d8" stroke-width="2" fill="none"/></svg>April 2015</li>
    <li><svg viewBox="0 0 14 14"><path d="M2 2l5 5-5 5M7 2l5 5-5 5" stroke="#3a93d8" stroke-width="2" fill="none"/></svg>March 2015</li>
    <li><svg viewBox="0 0 14 14"><path d="M2 2l5 5-5 5M7 2l5 5-5 5" stroke="#3a93d8" stroke-width="2" fill="none"/></svg>February 2015</li>
    <li><svg viewBox="0 0 14 14"><path d="M2 2l5 5-5 5M7 2l5 5-5 5" stroke="#3a93d8" stroke-width="2" fill="none"/></svg>January 2015</li>
    <li><svg viewBox="0 0 14 14"><path d="M2 2l5 5-5 5M7 2l5 5-5 5" stroke="#3a93d8" stroke-width="2" fill="none"/></svg>September 2014</li>
    <li><svg viewBox="0 0 14 14"><path d="M2 2l5 5-5 5M7 2l5 5-5 5" stroke="#3a93d8" stroke-width="2" fill="none"/></svg>June 2014</li>
    <li><svg viewBox="0 0 14 14"><path d="M2 2l5 5-5 5M7 2l5 5-5 5" stroke="#3a93d8" stroke-width="2" fill="none"/></svg>May 2014</li>
    <li><svg viewBox="0 0 14 14"><path d="M2 2l5 5-5 5M7 2l5 5-5 5" stroke="#3a93d8" stroke-width="2" fill="none"/></svg>April 2014</li>
  </ul>
</aside>

<aside class="widget abs" style="top:1797px;height:354px">
  <h3 class="band">Categories</h3>
  <ul class="list">
    <li><svg viewBox="0 0 14 14"><path d="M2 2l5 5-5 5M7 2l5 5-5 5" stroke="#3a93d8" stroke-width="2" fill="none"/></svg>21 Day Sweet Reset</li>
    <li><svg viewBox="0 0 14 14"><path d="M2 2l5 5-5 5M7 2l5 5-5 5" stroke="#3a93d8" stroke-width="2" fill="none"/></svg>Adrenal Fatigue</li>
    <li><svg viewBox="0 0 14 14"><path d="M2 2l5 5-5 5M7 2l5 5-5 5" stroke="#3a93d8" stroke-width="2" fill="none"/></svg>Articles</li>
    <li><svg viewBox="0 0 14 14"><path d="M2 2l5 5-5 5M7 2l5 5-5 5" stroke="#3a93d8" stroke-width="2" fill="none"/></svg>DIY</li>
    <li><svg viewBox="0 0 14 14"><path d="M2 2l5 5-5 5M7 2l5 5-5 5" stroke="#3a93d8" stroke-width="2" fill="none"/></svg>Essential Oils</li>
    <li><svg viewBox="0 0 14 14"><path d="M2 2l5 5-5 5M7 2l5 5-5 5" stroke="#3a93d8" stroke-width="2" fill="none"/></svg>Real Food</li>
    <li><svg viewBox="0 0 14 14"><path d="M2 2l5 5-5 5M7 2l5 5-5 5" stroke="#3a93d8" stroke-width="2" fill="none"/></svg>Uncategorized</li>
  </ul>
</aside>

<aside class="promo abs">
  <div class="promo-inner">
    <p class="promo-head"><span class="light">Need</span> Extra Support<br><span class="light">to</span> Rock <span class="light">your</span><br><span class="blue">21-Day Sweet Reset?</span></p>
    <div class="promo-products" role="img" aria-label="Product photo of program books and guides"></div>
    <div class="promo-badge"></div>
    <p class="promo-tag">I'm here to help</p>
    <div class="promo-btn">TELL ME MORE!</div>
  </div>
</aside>

<!-- footer -->
<footer class="footer-links abs">
  <div class="footer-col" style="left:123px"><h4>How We Help</h4><ul><li>Lead Generation</li><li>Tactics Management</li><li>Start-Up Website</li><li>Website Facelifts</li></ul></div>
  <div class="footer-col" style="left:403px"><h4>Services</h4><ul><li>Social Media Coaching</li><li>Website Analysis</li><li>Site Builder Website Design</li><li>Newsletters</li></ul></div>
  <div class="footer-col" style="left:682px"><h4>Results</h4><ul><li>Testimonials</li><li>B2B Companies</li><li>Contractors &amp; Construction</li><li>Manufacturing</li></ul></div>
  <div class="footer-col" style="left:939px"><h4>Support</h4><ul><li>Why Choose Fernpath</li><li>Our Culture</li><li>Our Team</li><li>Sitemap</li></ul></div>
</footer>
<div class="footer-bar abs">
  <p class="legal">Privacy Policy | Terms of Use | About Us | Sitemap<br>Copyright © 2015 All rights reserved.</p>
  <span class="social" style="left:860px;background:#3b5998"></span>
  <span class="social" style="left:920px;background:#2aa3e0"></span>
  <span class="social" style="left:980px;background:#d34836"></span>
  <span class="social" style="left:1040px;background:#1f7bb6"></span>
</div>

</body>
</html>
```